business card

Business card for new business.
Red and black corporate colors.
Card can have an Indsutrial feel to it. Feel free to add Rust, Bolted steel, or graphics as you see fit. We provide highly specialized services to the below mentioned industries.
Keep information out of corners so that if I want I can choose rounded corners.
Information
- front. name - title - phone - email
- Rear
Fabrication - Pipeline - Utilities - Marine - Forestry
Regina - Saskatoon - Prince George - Kamloops - Winnipeg

```html
<!DOCTYPE html>
<html lang="en">
<head>
<meta charset="utf-8">
<title>Framewell business card</title>
<link href="https://fonts.googleapis.com/css2?family=Open+Sans:wght@400;600;800&display=swap" rel="stylesheet">
<style>
  :root {
    --stage: #e6e3e0;
    --card: #161616;
    --card-edge: #1f1f1f;
    --red: #e0212b;
    --grey: #8a8a8a;
    --light: #c9c9c9;
    --white: #ffffff;
  }
  * { margin: 0; padding: 0; box-sizing: border-box; }
  html, body {
    width: 1200px; height: 864px; overflow: hidden;
    background: var(--stage);
    font-family: "Open Sans", Arial, sans-serif;
  }
  .stage {
    width: 1200px; height: 864px;
    display: flex; flex-direction: column;
    align-items: center; justify-content: center; gap: 40px;
  }
  .card {
    position: relative;
    width: 640px; height: 366px;
    background: linear-gradient(160deg, var(--card-edge), var(--card));
    box-shadow: 0 10px 28px rgba(0,0,0,.25);
    overflow: hidden;
  }
  .wordmark {
    display: flex; align-items: center; gap: 12px;
    white-space: nowrap;
  }
  .wordmark-square {
    width: 18px; height: 18px; background: var(--red); flex: none;
  }
  .wordmark-name {
    font-weight: 800; color: var(--grey);
    letter-spacing: 1px; text-transform: uppercase;
  }

  /* back */
  .card-back .wordmark {
    position: absolute; left: 50%; top: 92px; transform: translateX(-50%);
  }
  .card-back .wordmark-name { font-size: 48px; }
  .sectors {
    position: absolute; left: 40px; right: 40px; top: 196px;
    text-align: center; color: var(--light);
    font-size: 17px; line-height: 26px;
  }
  .sectors .dot { color: var(--red); padding: 0 5px; }

  /* front */
  .card-front .wordmark {
    position: absolute; right: 56px; top: 78px;
  }
  .card-front .wordmark-name { font-size: 40px; }
  .person {
    position: absolute; left: 56px; top: 150px;
  }
  .person-name {
    color: var(--red); font-weight: 600; font-size: 20px;
    text-transform: uppercase; letter-spacing: .5px;
  }
  .person-title {
    color: var(--white); font-size: 14px; text-transform: uppercase;
    margin-top: 2px;
  }
  .rule {
    position: absolute; left: 56px; right: 56px; top: 212px;
    height: 2px; background: var(--white);
  }
  .contacts {
    position: absolute; left: 56px; top: 228px;
    list-style: none;
  }
  .contacts li {
    display: flex; align-items: center; gap: 10px;
    color: var(--white); font-size: 16px; line-height: 28px;
  }
  .contacts svg { width: 15px; height: 15px; fill: var(--red); flex: none; }
</style>
</head>
<body>
<main class="stage">
  <section class="card card-back">
    <div class="wordmark">
      <span class="wordmark-square"></span>
      <span class="wordmark-name">Framewell</span>
    </div>
    <p class="sectors">
      Fabrication<span class="dot">•</span>Pipeline<span class="dot">•</span>Utilities<span class="dot">•</span>Marine<br>
      Forestry<span class="dot">•</span>Regina<span class="dot">•</span>Saskatoon<span class="dot">•</span>Prince George<br>
      Kamloops<span class="dot">•</span>Winnipeg
    </p>
  </section>

  <section class="card card-front">
    <div class="wordmark">
      <span class="wordmark-square"></span>
      <span class="wordmark-name">Framewell</span>
    </div>
    <div class="person">
      <p class="person-name">Mark Ellison</p>
      <p class="person-title">President</p>
    </div>
    <div class="rule"></div>
    <ul class="contacts">
      <li>
        <svg viewBox="0 0 16 16" aria-hidden="true"><path d="M3 1h3l1.5 4-2 1.3a9 9 0 0 0 4.2 4.2L11 8.5l4 1.5v3a2 2 0 0 1-2 2A12 12 0 0 1 1 3a2 2 0 0 1 2-2z"/></svg>
        555 0142 7788
      </li>
      <li>
        <svg viewBox="0 0 16 16" aria-hidden="true"><path d="M1 3h14v10H1z M1 3l7 6 7-6" stroke="#161616" stroke-width="1.2"/></svg>
        mark@framewell.com
      </li>
      <li>
        <svg viewBox="0 0 16 16" aria-hidden="true"><circle cx="8" cy="8" r="7"/><path d="M1 8h14M8 1c-3 3.5-3 10.5 0 14M8 1c3 3.5 3 10.5 0 14" stroke="#161616" stroke-width="1.1" fill="none"/></svg>
        www.framewell.com
      </li>
    </ul>
  </section>
</main>
</body>
</html>
```